CopperWanderer Stretching and Strength

We need a application design for a our first IOS application. the goal of the application is to categorize stretching and strength routines for triathlon.

We would like to see designs that use the color orange.

The design of the application should be compliant with the last version of the IOS Mobile.

For this first design we need the folowing pages:

1- Sign up
2- Log in
3- Home
4- View Exercises
5- Do it
6- Profile

The description of each page is in the attached document.

We need a logo design for the application. The logo should express that mission of the application that is for stretch and strength training for Triathlon.

We will use https://pellavokit.example to develop the application, if you have any experience of the limitation that this technology have it will be a plus.

If you have any question please feel free to contact us.

Reason: We will extend the deadline to be sure that we select the best design from all of you. we will take the final decision next Tuesday.

Target Market(s)

The market for my aplicación is the Running a Triathlon world.

Logo Text

CopperWanderer

Font styles to use
Serif

Colors
f37122
ffffff
dcdcdc

Requirements
Must have
• In some future we will add more features in the menu. We should considere it for the design.
• The designs should include all the screens in the power point.

```html
<!DOCTYPE html>
<html lang="en">
<head>
<meta charset="utf-8">
<title>CopperWanderer – Log In</title>
<link href="https://fonts.googleapis.com/css2?family=Roboto:ital,wght@0,400;0,500;0,700;1,400&display=swap" rel="stylesheet">
<style>
  :root {
    --backdrop: #d6e4f0;
    --screen-bg: #ebeef2;
    --field-bg: #ffffff;
    --text-muted: #6b6f75;
    --text-soft: #85898f;
    --orange: #f37122;
    --social-blue: #1e5fb3;
    --white: #ffffff;
    --icon-grey: #7a7d82;
    --divider: #dcdcdc;
    --water-light: #6fb8bf;
    --water-deep: #1f96a3;
  }
  * { box-sizing: border-box; margin: 0; padding: 0; }
  html, body {
    width: 1200px; height: 1200px; overflow: hidden;
    background: var(--backdrop);
    font-family: "Roboto", sans-serif;
  }
  .screen {
    position: absolute; left: 263px; top: 0;
    width: 674px; height: 1200px;
    background: var(--screen-bg);
    overflow: hidden;
  }
  .hero {
    position: absolute; left: 0; top: 0; width: 674px; height: 457px;
    background: linear-gradient(180deg, var(--water-light) 0%, var(--water-deep) 100%);
  }
  .status-bar {
    position: absolute; left: 0; top: 0; width: 674px; height: 44px;
    display: flex; align-items: center; justify-content: space-between;
    padding: 0 10px; color: var(--white); font-size: 19px;
  }
  .status-left, .status-right { display: flex; align-items: center; gap: 8px; }
  .status-time { position: absolute; left: 0; right: 0; text-align: center; pointer-events: none; }
  .pager {
    position: absolute; top: 420px; left: 0; width: 674px;
    display: flex; justify-content: center; gap: 12px;
  }
  .pager span { width: 11px; height: 11px; border-radius: 50%; background: var(--white); }
  .pager span.active { background: var(--orange); }
  .field {
    position: absolute; left: 45px; width: 583px; height: 67px;
    background: var(--field-bg);
    box-shadow: 0 2px 3px rgba(0,0,0,0.12);
    display: flex; align-items: center; justify-content: space-between;
    padding: 0 26px; font-size: 23px; color: var(--text-muted);
  }
  .field-user { top: 498px; }
  .field-pass { top: 580px; }
  .options {
    position: absolute; left: 45px; width: 583px; top: 680px; height: 28px;
    display: flex; align-items: center; justify-content: space-between;
    font-size: 21px; color: var(--text-muted);
  }
  .remember { display: flex; align-items: center; gap: 16px; }
  .checkbox { width: 25px; height: 25px; border: 2px solid var(--icon-grey); border-radius: 2px; }
  .forgot { font-style: italic; color: var(--text-soft); }
  .login-button {
    position: absolute; left: 45px; top: 766px; width: 583px; height: 73px;
    border-radius: 37px; background: var(--orange);
    box-shadow: 0 3px 5px rgba(0,0,0,0.18);
    color: var(--white); font-size: 25px; font-weight: 700;
    display: flex; align-items: center; justify-content: center; letter-spacing: 0.5px;
  }
  .signup-line {
    position: absolute; left: 0; width: 674px; top: 970px;
    text-align: center; font-size: 20px; color: var(--text-muted);
  }
  .signup-line a { color: var(--orange); font-weight: 500; text-decoration: underline; }
  .or-badge {
    position: absolute; left: 322px; top: 1039px; width: 30px; height: 30px;
    border-radius: 50%; background: var(--divider);
    font-size: 13px; color: #444; font-weight: 500;
    display: flex; align-items: center; justify-content: center;
  }
  .social-bar {
    position: absolute; left: 0; top: 1118px; width: 674px; height: 82px; display: flex;
  }
  .social {
    width: 337px; height: 82px; display: flex; align-items: center; gap: 16px;
    padding-left: 22px; font-size: 25px; white-space: nowrap;
  }
  .social-circlely { background: var(--social-blue); color: var(--white); }
  .social-postly { background: var(--white); color: #333; padding-left: 44px; border-top: 1px solid var(--divider); }
  .social-dot { width: 50px; height: 50px; border-radius: 50%; flex: none; }
  .social-circlely .social-dot { background: var(--white); }
  .social-postly .social-dot { background: #bdbdbd; }
  .social em { font-size: 21px; }
</style>
</head>
<body>
<main class="screen">
  <div class="hero" role="img" aria-label="Photo of a swimmer doing butterfly stroke in a turquoise pool"></div>

  <div class="status-bar">
    <div class="status-left">
      <svg width="50" height="12" viewBox="0 0 50 12" aria-hidden="true">
        <circle cx="5" cy="6" r="4.5" fill="#fff"/><circle cx="15" cy="6" r="4.5" fill="#fff"/><circle cx="25" cy="6" r="4.5" fill="#fff"/>
        <circle cx="35" cy="6" r="4" fill="none" stroke="#fff" stroke-width="1"/><circle cx="45" cy="6" r="4" fill="none" stroke="#fff" stroke-width="1"/>
      </svg>
      <span>LUMA</span>
      <svg width="20" height="16" viewBox="0 0 20 16" aria-hidden="true">
        <path d="M1 5 A13 13 0 0 1 19 5" fill="none" stroke="#fff" stroke-width="2"/>
        <path d="M4.5 8.5 A8 8 0 0 1 15.5 8.5" fill="none" stroke="#fff" stroke-width="2"/>
        <path d="M10 15 L7 11.5 A4 4 0 0 1 13 11.5 Z" fill="#fff"/>
      </svg>
    </div>
    <div class="status-time">4:21 PM</div>
    <div class="status-right">
      <span>100%</span>
      <svg width="40" height="16" viewBox="0 0 40 16" aria-hidden="true">
        <rect x="0.5" y="0.5" width="35" height="15" rx="3" fill="none" stroke="#fff"/>
        <rect x="2.5" y="2.5" width="31" height="11" rx="1.5" fill="#fff"/>
        <rect x="37" y="5" width="2.5" height="6" rx="1" fill="#fff"/>
      </svg>
    </div>
  </div>

  <div class="pager"><span></span><span class="active"></span><span></span><span></span><span></span></div>

  <div class="field field-user">
    <span>User Name</span>
    <svg width="22" height="26" viewBox="0 0 22 26" aria-hidden="true">
      <circle cx="11" cy="7" r="6" fill="var(--icon-grey)"/>
      <path d="M0 26 V21 A8 8 0 0 1 8 14 H14 A8 8 0 0 1 22 21 V26 Z" fill="var(--icon-grey)"/>
    </svg>
  </div>
  <div class="field field-pass">
    <span>Password</span>
    <svg width="22" height="27" viewBox="0 0 22 27" aria-hidden="true">
      <path d="M5 12 V8 A6 6 0 0 1 17 8 V12" fill="none" stroke="var(--icon-grey)" stroke-width="3"/>
      <rect x="0" y="11" width="22" height="16" rx="2" fill="var(--icon-grey)"/>
      <circle cx="11" cy="18" r="2.5" fill="#fff"/>
    </svg>
  </div>

  <div class="options">
    <label class="remember"><span class="checkbox"></span><span>Remamber Me</span></label>
    <span class="forgot">Forgot Password?</span>
  </div>

  <div class="login-button">LOG IN</div>

  <p class="signup-line">You have not any account yet? <a>SIGN UP</a> now</p>

  <div class="or-badge">OR</div>

  <div class="social-bar">
    <div class="social social-circlely"><span class="social-dot"></span><span>Log in <em>with</em> Circlely</span></div>
    <div class="social social-postly"><span class="social-dot"></span><span>Log in <em>with</em> Postly</span></div>
  </div>
</main>
</body>
</html>
```